Consulting Company PowerPoint Template Design

We are looking for an updated PowerPoint template design or our 55 person energy consulting firm (K7) based in San Francisco (www.kseven-example.com). We would like two versions of the same PowerPoint template in a 16:9 and 4:3 format with our existing logo.

We have an existing color scheme and template and are seeking your help to polish/update the template design for wide format and create a flexible template that is easy to use with content from Excel and Word. Our current template, and a couple of examples that we like are attached.

Specific requests include:

• Dark background for slide title
• A narrow section header
• Maximizing white space for content
• A limited number of well designed Master template layouts to choose from
• A selection of title and section header slides that are not San Francisco specific with some variety to chose from ideally with a focus on energy or nature, graphics/visuals.

For examples of energy specific templates see:
https://www.brightslidehub.example/energy/powerpoint-templates/0.html

Requirements
Must have
• Must use our logo but open to other designs, fonts, and styles for the PowerPoint template.
• Please use our existing color scheme found in the attached Excel file.
• Also we would like the ability to easily copy and paste from our existing/original template to the new template. In other words we would like backward compatibility to apply the new template format to our old PowerPoints that use our existing template.

```html
<!DOCTYPE html>
<html lang="en">
<head>
<meta charset="utf-8">
<title>K7 – Mission, Vision, Portfolio</title>
<link href="https://fonts.googleapis.com/css2?family=Exo+2:wght@400;500;600&display=swap" rel="stylesheet">
<style>
  :root {
    --navy: #0b4b6d;
    --gold: #d6b36e;
    --ink: #111111;
    --muted: #8a8a8a;
    --ring: #d4d4d4;
    --white: #ffffff;
  }
  * { margin: 0; padding: 0; box-sizing: border-box; }
  html, body { width: 1200px; height: 900px; overflow: hidden; background: var(--white); }
  body { font-family: "Exo 2", sans-serif; position: relative; }

  .title-bar {
    position: absolute; left: 0; top: 0; width: 1200px; height: 68px;
    background: var(--navy);
  }
  .title-accent { position: absolute; left: 0; top: 68px; }
  .slide-title {
    position: absolute; left: 17px; top: 10px;
    font-size: 35px; font-weight: 500; letter-spacing: 0.5px;
    color: var(--white);
  }
  .slide-title .highlight { color: var(--gold); }

  .brand {
    position: absolute; left: 1108px; top: 4px; width: 80px; height: 80px;
    border-radius: 50%; background: var(--white);
    border: 4px solid var(--navy);
    display: flex; align-items: center; justify-content: center;
    font-size: 30px; font-weight: 600; color: var(--navy);
  }

  .pillars { position: absolute; left: 0; top: 305px; width: 1200px; }
  .pillar {
    position: absolute; top: 0; width: 320px;
    display: flex; flex-direction: column; align-items: center;
  }
  .pillar--mission { left: 72px; }
  .pillar--vision { left: 450px; }
  .pillar--portfolio { left: 850px; }
  .pillar-emblem { width: 210px; height: 210px; }
  .pillar-heading {
    margin-top: 42px; font-size: 38px; font-weight: 500;
    color: var(--ink); letter-spacing: 0.3px; white-space: nowrap;
  }
  .pillar--vision .pillar-heading { color: var(--navy); }
  .pillar-text {
    margin-top: 12px; width: 320px; text-align: center;
    font-size: 20px; line-height: 30px; color: var(--muted);
  }

  .footer-bar {
    position: absolute; left: 0; top: 855px; width: 1200px; height: 45px;
    background: var(--navy);
  }
  .footer-name {
    position: absolute; left: 9px; top: 6px;
    font-size: 26px; font-weight: 600; color: var(--white); white-space: nowrap;
  }
  .page-tab { position: absolute; left: 1090px; top: 855px; }
  .page-number {
    position: absolute; left: 1137px; top: 862px;
    font-size: 20px; color: var(--white);
  }
</style>
</head>
<body>
  <header class="title-bar">
    <h1 class="slide-title"><span class="highlight">PROJECT</span> TITLE HERE</h1>
  </header>
  <svg class="title-accent" width="1200" height="10" viewBox="0 0 1200 10">
    <polygon points="0,0 1112,0 1100,8 0,8" fill="var(--gold)"/>
  </svg>
  <div class="brand">K7</div>

  <main class="pillars">
    <section class="pillar pillar--mission">
      <svg class="pillar-emblem" viewBox="0 0 210 210" aria-hidden="true">
        <circle cx="105" cy="105" r="95" fill="none" stroke="var(--ring)" stroke-width="1.5"/>
        <line x1="172" y1="38" x2="201" y2="9" stroke="var(--ring)" stroke-width="1.5"/>
        <line x1="38" y1="172" x2="9" y2="201" stroke="var(--ring)" stroke-width="1.5"/>
        <g fill="none" stroke="var(--ink)" stroke-width="3" stroke-linejoin="round">
          <rect x="76" y="56" width="48" height="92" rx="4"/>
          <line x1="76" y1="66" x2="124" y2="66"/>
          <line x1="76" y1="132" x2="124" y2="132"/>
          <circle cx="100" cy="140" r="4"/>
          <line x1="96" y1="61" x2="104" y2="61"/>
          <path d="M100 78 H148 V106 H114 L104 116 V106 H100 Z" fill="var(--white)"/>
          <line x1="110" y1="88" x2="124" y2="88"/>
          <line x1="110" y1="96" x2="138" y2="96"/>
        </g>
      </svg>
      <h2 class="pillar-heading">OUR MISSION</h2>
      <p class="pillar-text">There are many variations of passages of Lorem Ipsum avail-able, but the majority have suf-fered alteration in some form, by injected humour,</p>
    </section>

    <section class="pillar pillar--vision">
      <svg class="pillar-emblem" viewBox="0 0 210 210" aria-hidden="true">
        <circle cx="105" cy="105" r="95" fill="none" stroke="var(--navy)" stroke-width="3"/>
        <line x1="172" y1="38" x2="201" y2="9" stroke="var(--navy)" stroke-width="3"/>
        <line x1="38" y1="172" x2="9" y2="201" stroke="var(--navy)" stroke-width="3"/>
        <g fill="none" stroke="var(--navy)" stroke-width="3" stroke-linejoin="round">
          <rect x="85" y="56" width="48" height="92" rx="4"/>
          <line x1="85" y1="66" x2="133" y2="66"/>
          <line x1="85" y1="132" x2="133" y2="132"/>
          <circle cx="109" cy="140" r="4"/>
          <line x1="105" y1="61" x2="113" y2="61"/>
          <circle cx="98" cy="93" r="20" fill="var(--white)"/>
          <line x1="84" y1="107" x2="57" y2="134"/>
        </g>
      </svg>
      <h2 class="pillar-heading">OUR VISION</h2>
      <p class="pillar-text">There are many variations of passages of Lorem Ipsum avail-able, but the majority have suf-fered alteration in some form, by injected humour,</p>
    </section>

    <section class="pillar pillar--portfolio">
      <svg class="pillar-emblem" viewBox="0 0 210 210" aria-hidden="true">
        <circle cx="105" cy="105" r="95" fill="none" stroke="var(--ring)" stroke-width="1.5"/>
        <line x1="172" y1="38" x2="201" y2="9" stroke="var(--ring)" stroke-width="1.5"/>
        <line x1="38" y1="172" x2="9" y2="201" stroke="var(--ring)" stroke-width="1.5"/>
        <g fill="none" stroke="var(--ink)" stroke-width="3" stroke-linecap="round">
          <circle cx="105" cy="103" r="46"/>
          <path d="M72 134 Q105 110 138 134"/>
          <line x1="105" y1="67" x2="105" y2="72"/>
          <line x1="80" y1="77" x2="83" y2="81"/>
          <line x1="130" y1="77" x2="127" y2="81"/>
          <line x1="69" y1="99" x2="74" y2="100"/>
          <line x1="141" y1="99" x2="136" y2="100"/>
          <circle cx="103" cy="104" r="5"/>
          <line x1="107" y1="100" x2="124" y2="82"/>
        </g>
      </svg>
      <h2 class="pillar-heading">OUR PORTFOLIO</h2>
      <p class="pillar-text">There are many variations of passages of Lorem Ipsum avail-able, but the majority have suf-fered alteration in some form, by injected humour,</p>
    </section>
  </main>

  <footer class="footer-bar">
    <p class="footer-name">Kinetic+Climate Advisory Group</p>
  </footer>
  <svg class="page-tab" width="110" height="45" viewBox="0 0 110 45">
    <polygon points="18,0 110,0 110,45 28,45 4,20" fill="var(--gold)"/>
  </svg>
  <span class="page-number">01</span>
</body>
</html>
```